Computer Company needs a Business card design

We need a business card design for our business. We assist people to transition to the KVS (Kestrel Vantage Scheme). The Verandal Crown Office-owned kvs™ network is a brand new telecommunications network currently being rolled out across Australia, giving access to a reliable broadband connection. Our niche market will predominantly be domestic customers in the 50+ age bracket. The assistance that we provide is everything from arranging the equipment, arranging the plan and contract term, appointment times, final testing of the network and any tweaks that need to be made. We basically PM the transition from start to finish. The business card design should be minimalist, should communicate loyalty and stability, should be easy to read and clearly explain what we do. We have asked for front and back. However, the back of the card does not have to include much information at all. It could be just a small design, or a repeat of our phone number. Up to you. The attached file only says what is required on the card. It does not specify where to arrange the text, what fonts to use, etc etc. As much as we would like to give you more info, due to our very limited design ability, we are not really able to send you any rough, or otherwise, designs of what we are after. Hopefully the above description is enough for you.

```html
<!DOCTYPE html>
<html lang="en">
<head>
<meta charset="utf-8">
<title>Steadyline Connect – Business Card</title>
<link rel="stylesheet" href="https://fonts.googleapis.com/css2?family=Jost:wght@400;600&display=swap">
<style>
  :root {
    --bg: #d6d6d6;
    --brand-blue: #0a85ae;
    --card-white: #f7f7f7;
    --ink-grey: #555a5e;
    --white: #ffffff;
  }
  * { box-sizing: border-box; margin: 0; padding: 0; }
  html, body {
    width: 1200px; height: 960px; overflow: hidden;
    background: var(--bg);
    font-family: "Jost", "Century Gothic", sans-serif;
  }
  .stage { position: relative; width: 1200px; height: 960px; }
  .card {
    position: absolute; left: 320px; width: 600px; height: 340px;
  }
  .card--front {
    top: 108px; background: var(--brand-blue);
    display: flex; align-items: center; justify-content: center;
  }
  .card--back { top: 494px; background: var(--card-white); }
  .wordmark {
    font-weight: 600; letter-spacing: 0; white-space: nowrap;
  }
  .card--front .wordmark { color: var(--white); font-size: 46px; margin-top: -2px; }
  .card--back .wordmark {
    position: absolute; left: 50px; top: 80px;
    color: var(--brand-blue); font-size: 46px;
  }
  .contact-list {
    position: absolute; left: 52px; top: 217px; list-style: none;
    color: var(--ink-grey); font-size: 15.5px; line-height: 19.5px;
  }
  .contact-list li { display: flex; align-items: center; gap: 9px; }
  .contact-list svg { width: 12px; height: 12px; fill: var(--brand-blue); flex: none; }
  .name-badge {
    position: absolute; right: 0; top: 216px; width: 215px; height: 64px;
    background: var(--brand-blue); color: var(--white);
    text-align: right; padding: 9px 28px 0 0;
  }
  .name-badge__name { font-weight: 600; font-size: 20px; letter-spacing: 0.6px; line-height: 24px; }
  .name-badge__role { font-size: 15px; letter-spacing: 0.4px; line-height: 20px; }
</style>
</head>
<body>
<main class="stage">
  <section class="card card--front" aria-label="Card front">
    <p class="wordmark">Steadyline Connect</p>
  </section>

  <section class="card card--back" aria-label="Card back">
    <p class="wordmark">Steadyline Connect</p>

    <ul class="contact-list">
      <li>
        <svg viewBox="0 0 24 24" aria-hidden="true"><path d="M6.6 10.8a15.1 15.1 0 0 0 6.6 6.6l2.2-2.2a1 1 0 0 1 1-.25 11.4 11.4 0 0 0 3.6.57 1 1 0 0 1 1 1V20a1 1 0 0 1-1 1A17 17 0 0 1 3 4a1 1 0 0 1 1-1h3.5a1 1 0 0 1 1 1c0 1.25.2 2.45.57 3.57a1 1 0 0 1-.25 1z"/></svg>
        <span>0400982715</span>
      </li>
      <li>
        <svg viewBox="0 0 24 24" aria-hidden="true"><path d="M2 5h20v14H2z"/><path d="M3.5 6.5 12 13l8.5-6.5" fill="none" stroke="#fff" stroke-width="1.6"/></svg>
        <span>rowan@steadylineconnect.com.au</span>
      </li>
      <li>
        <svg viewBox="0 0 24 24" aria-hidden="true"><circle cx="12" cy="12" r="10"/><path d="M2 12h20M12 2c3 3 3 17 0 20M12 2c-3 3-3 17 0 20" fill="none" stroke="#fff" stroke-width="1.4"/></svg>
        <span>www.steadylineconnect.com.au</span>
      </li>
    </ul>

    <div class="name-badge">
      <p class="name-badge__name">ROWAN PELLET</p>
      <p class="name-badge__role">CEO/FOUNDER</p>
    </div>
  </section>
</main>
</body>
</html>
```